MRT Property - Business Cards

Looking for a business card & general letterhead, signage etc design for our new logo.

Colours:
000a20
0056a2
00b5ef
0088ce
68cef2

Fonts:
Poppins
Karla

Please keep look and feel of new brand - example in the zip package I sent.

```html
<!DOCTYPE html>
<html lang="en">
<head>
<meta charset="utf-8">
<title>MRT Property – Business Cards</title>
<link href="https://fonts.googleapis.com/css2?family=Montserrat:wght@400;500;600;700&display=swap" rel="stylesheet">
<style>
  :root {
    --navy: #000a20;
    --brand-blue: #0056a2;
    --sky: #00b5ef;
    --mid-blue: #0088ce;
    --light-blue: #68cef2;
    --name-blue: #29a9e3;
    --card-back: #1388d0;
    --back-mark: #0d6fb4;
    --text-grey: #3a3a3a;
    --icon-grey: #4a6a7e;
    --page: #d9d4cc;
    --card-white: #ffffff;
  }
  * { margin: 0; padding: 0; box-sizing: border-box; }
  html, body { width: 900px; height: 1200px; overflow: hidden; }
  body {
    background: var(--page);
    font-family: "Montserrat", Arial, sans-serif;
    position: relative;
  }
  .card {
    position: absolute;
    left: 80px;
    width: 742px;
    height: 440px;
    border-radius: 36px;
    box-shadow: 0 6px 10px rgba(0,0,0,0.35);
  }
  .card--front { top: 132px; background: var(--card-white); }
  .card--back { top: 638px; background: var(--card-back); }

  .brand {
    position: absolute;
    display: flex;
    align-items: center;
    gap: 14px;
    font-weight: 700;
    white-space: nowrap;
  }
  .brand__dot { border-radius: 50%; flex: none; }
  .card--front .brand { left: 34px; top: 216px; font-size: 40px; color: var(--brand-blue); }
  .card--front .brand__dot { width: 34px; height: 34px; background: var(--brand-blue); }
  .card--back .brand { left: 76px; top: 180px; font-size: 70px; color: var(--back-mark); }
  .card--back .brand__dot { width: 58px; height: 58px; background: var(--back-mark); }

  .divider {
    position: absolute;
    left: 409px; top: 138px;
    width: 2px; height: 182px;
    background: var(--sky);
  }
  .contact { position: absolute; left: 457px; top: 132px; }
  .contact__name { font-size: 27px; font-weight: 600; color: var(--name-blue); line-height: 1.1; }
  .contact__role { font-size: 16px; color: var(--text-grey); margin-top: 1px; }
  .contact__list { list-style: none; margin-top: 24px; }
  .contact__item {
    display: flex; align-items: center; gap: 11px;
    font-size: 16px; color: var(--text-grey); height: 23px;
  }
  .contact__icon { width: 14px; height: 14px; fill: var(--icon-grey); flex: none; }
  .contact__address { margin-top: 12px; font-size: 16px; color: var(--text-grey); line-height: 20px; padding-left: 1px; }
</style>
</head>
<body>
  <section class="card card--front" aria-label="Business card front">
    <div class="brand"><span class="brand__dot"></span>MRT Property</div>
    <div class="divider"></div>
    <div class="contact">
      <div class="contact__name">Marcus Ellery</div>
      <div class="contact__role">Owner</div>
      <ul class="contact__list">
        <li class="contact__item">
          <svg class="contact__icon" viewBox="0 0 14 14" aria-hidden="true"><path d="M1 5c0-2 2-3 6-3s6 1 6 3v1h-3V5H4v1H1z"/><path d="M3 7h8l1.5 5h-11z"/></svg>
          215-555-0142
        </li>
        <li class="contact__item">
          <svg class="contact__icon" viewBox="0 0 14 14" aria-hidden="true"><path d="M1 3h12v1L7 8 1 4z"/><path d="M1 5.5l6 4 6-4V11H1z"/></svg>
          info@mrtproperty.com.au
        </li>
        <li class="contact__item">
          <svg class="contact__icon" viewBox="0 0 14 14" aria-hidden="true"><circle cx="7" cy="7" r="6"/></svg>
          www.mrtproperty.com.au
        </li>
      </ul>
      <div class="contact__address">48 Harbor View Road, Suite 210<br>Fairhill, PA 19000</div>
    </div>
  </section>

  <section class="card card--back" aria-label="Business card back">
    <div class="brand"><span class="brand__dot"></span>MRT Property</div>
  </section>
</body>
</html>
```